Bright Harbor Counseling Letterhead for hip modern business

I would like some ombre use of the colors in the logo hip letterhead that incorporates logo colors and feel, needs to connect with young professionals and college students. i need to be able to write letters to schools to excuse absences as well. i like color blocks on one side preferably using colors from the attached logo design.

Target Market(s)

high income young people, young adults and college students

Industry/Entity Type

mental health

Font styles to use
Serif
Sans Serif

Colors
0054AA
0677BA
7BADD7
CADEEF
E8F1F8
0094D4
00A9DD
6FCCEA
C7EBF8
E9F6FB
00AB8E
00BBA5
67D7C9
C6EFE9
E9F9F6
59FF00
82FF00
B8FF75
E3FFCB
F4FFEA
A7469A
B969AE
D3A5CF
EDDBEB
F8F0F9
6B429C
8869AF
B7A5CE
E3DAEB
F3F0F8

Requirements
Must have
• a modern hip feel, somewhat color

```html
<!DOCTYPE html>
<html lang="en">
<head>
<meta charset="utf-8">
<title>Bright Harbor Counseling Letterhead</title>
<link rel="stylesheet" href="https://fonts.googleapis.com/css2?family=Questrial&family=Arimo:wght@400&display=swap">
<style>
  :root {
    --backdrop: #2b2b2d;
    --paper: #ffffff;
    --ink: #4a4a4a;
    --ink-soft: #6d6d6d;
    --teal: #52c3b5;
    --purple: #9a6bb7;
    --orchid: #b46aae;
    --sky: #5cc4ea;
    --blue: #559fd6;
    --rose: #c060a4;
    --indigo: #6b77bb;
    --signature-tone: #e9e9ee;
  }
  * { box-sizing: border-box; margin: 0; padding: 0; }
  html, body {
    width: 1200px; height: 901px; overflow: hidden;
    background: var(--backdrop);
  }
  .letterhead {
    position: absolute; left: 296px; top: 20px;
    width: 608px; height: 860px;
    background: var(--paper);
    overflow: hidden;
    font-family: "Arimo", Arial, sans-serif;
    color: var(--ink);
  }
  .header-bar { position: absolute; height: 10px; }
  .header-bar--purple { left: 0; top: 122px; width: 232px; background: var(--purple); }
  .header-bar--teal { right: 0; top: 64px; width: 120px; background: var(--teal); }

  .brand { position: absolute; left: 246px; top: 40px; width: 240px; text-align: right; }
  .brand-dot {
    position: absolute; right: 0; top: -12px;
    width: 28px; height: 28px; border-radius: 50%; background: var(--purple);
  }
  .brand-name, .brand-sub {
    font-family: "Questrial", Arial, sans-serif; font-weight: 400; color: var(--ink-soft);
  }
  .brand-name { display: block; padding-top: 32px; font-size: 27px; line-height: 1; }
  .brand-sub { display: block; font-size: 11px; letter-spacing: 0.32em; margin-top: 4px; }

  .letter-body { position: absolute; left: 70px; right: 52px; top: 170px; }
  .letter-title {
    font-family: "Questrial", Arial, sans-serif; font-weight: 400;
    font-size: 22px; color: #333; margin-bottom: 10px;
  }
  .letter-body p { font-size: 8.6px; line-height: 1.38; margin-bottom: 22px; color: var(--ink); }

  .signature {
    position: absolute; left: 150px; top: 700px;
    width: 150px; height: 58px; background: var(--signature-tone); border-radius: 4px;
  }

  .contact {
    position: absolute; left: 395px; top: 716px;
    border-left: 1.5px solid var(--teal); padding-left: 8px;
    font-size: 11px; line-height: 1.55; color: #222; list-style: none;
  }
  .contact li { display: flex; align-items: center; gap: 5px; }
  .contact svg { width: 9px; height: 9px; flex: none; }

  .color-blocks {
    position: absolute; left: -10px; right: -10px; bottom: 0; height: 18px;
    display: flex; gap: 8px;
  }
  .color-block { flex: 1; transform: skewX(-35deg); }
  .color-block--teal { background: var(--teal); }
  .color-block--orchid { background: var(--orchid); }
  .color-block--sky { background: var(--sky); }
  .color-block--blue { background: var(--blue); }
  .color-block--rose { background: var(--rose); }
  .color-block--indigo { background: var(--indigo); }
</style>
</head>
<body>
<main class="letterhead">
  <div class="header-bar header-bar--purple"></div>
  <div class="header-bar header-bar--teal"></div>

  <header class="brand">
    <span class="brand-dot"></span>
    <span class="brand-name">Bright Harbor</span>
    <span class="brand-sub">Counseling</span>
  </header>

  <section class="letter-body">
    <h1 class="letter-title">Lorem ipsum</h1>
    <p>Lorem ipsum dolor sit amet, consectetuer adipiscing elit, sed diam nonummy nibh euismod tincidunt ut laoreet dolore magna aliquam erat volutpat. Ut wisi enim ad minim veniam, quis nostrud exerci tation ullamcorper suscipit lobortis nisl ut aliquip ex ea commodo consequat. Duis autem vel eum iriure dolor in hendrerit in vulputate velit esse molestie consequat, vel illum dolore eu feugiat nulla facilisis at vero eros et accumsan et iusto odio dignissim qui blandit praesent luptatum zzril delenit augue duis dolore te feugait nulla facilisi.</p>
    <p>Lorem ipsum dolor sit amet, cons ectetuer adipiscing elit, sed diam nonummy nibh euismod tincidunt ut laoreet dolore magna aliquam erat volutpat. Ut wisi enim ad minim veniam, quis nostrud exerci tation ullamcorper suscipit lobortis nisl ut aliquip ex ea commodo consequat. Lorem ipsum dolor sit amet, consectetuer adipiscing elit, sed diam nonummy nibh euismod tincidunt ut laoreet dolore magna aliquam erat volutpat. Ut wisi enim ad minim veniam, quis nostrud exerci tation ullamcorper suscipit lobortis nisl ut aliquip ex ea commodo consequat. Duis autem vel eum iriure dolor in hendrerit in vulputate velit esse molestie consequat, vel illum dolore eu feugiat nulla facilisis at vero eros et accumsan et iusto odio dignissim qui blandit praesent luptatum zzril delenit augue duis dolore te feugait nulla facilisi. Lorem ipsum dolor sit amet, cons ectetuer adipiscing elit, sed diam nonummy nibh euismod tincidunt ut laoreet dolore magna aliquam erat volutpat. Ut wisi enim ad minim veniam, quis nostrud exerci tation ullamcorper suscipit lobortis nisl ut aliquip ex ea commodo consequat.</p>
    <p>Lorem ipsum dolor sit amet, consectetuer adipiscing elit, sed diam nonummy nibh euismod tincidunt ut laoreet dolore magna aliquam erat volutpat. Ut wisi enim ad minim veniam, quis nostrud exerci tation ullamcorper suscipit lobortis nisl ut aliquip ex ea commodo consequat. Duis autem vel eum iriure dolor in hendrerit in vulputate velit esse molestie consequat, vel illum dolore eu feugiat nulla facilisis at vero eros et accumsan et iusto odio dignissim qui blandit praesent luptatum zzril delenit augue duis dolore te feugait nulla facilisi. Lorem ipsum dolor sit amet, cons ectetuer adipiscing elit, sed diam nonummy nibh euismod tincidunt ut laoreet dolore magna aliquam erat volutpat. Ut wisi enim ad minim veniam, quis nostrud exerci tation ullamcorper suscipit lobortis nisl ut aliquip ex ea commodo consequat. Duis autem vel eum iriure dolor in hendrerit in vulputate velit esse molestie consequat, vel illum dolore eu feugiat nulla facilisis at vero eros et accumsan et iusto odio dignissim qui blandit praesent luptatum zzril delenit augue duis dolore te feugait nulla facilisi.</p>
    <p>Lorem ipsum dolor sit amet, cons ectetuer adipiscing elit, sed diam nonummy nibh euismod tincidunt ut laoreet dolore magna aliquam erat volutpat. Ut wisi enim ad minim veniam, quis nostrud exerci tation ullamcorper suscipit lobortis nisl ut aliquip ex ea commodo consequat.</p>
  </section>

  <div class="signature" role="img" aria-label="Handwritten signature of the sender"></div>

  <ul class="contact">
    <li><svg viewBox="0 0 10 10" aria-hidden="true"><circle cx="5" cy="5" r="5" fill="#9a6bb7"/><path d="M3.2 2.6l1 1-.5.7a3 3 0 0 0 2 2l.7-.5 1 1-.7.7C4.8 7.2 2.8 5.2 2.6 3.3z" fill="#fff"/></svg>555-014-2290</li>
    <li><svg viewBox="0 0 10 10" aria-hidden="true"><circle cx="5" cy="5" r="5" fill="#9a6bb7"/><rect x="2.6" y="3.3" width="4.8" height="3.4" fill="none" stroke="#fff" stroke-width=".8"/><path d="M2.6 3.3L5 5.3l2.4-2" fill="none" stroke="#fff" stroke-width=".8"/></svg>hello@brightharbor.example</li>
    <li><svg viewBox="0 0 10 10" aria-hidden="true"><circle cx="5" cy="5" r="5" fill="#9a6bb7"/><path d="M5 2.2a1.9 1.9 0 0 0-1.9 1.9C3.1 5.6 5 7.8 5 7.8s1.9-2.2 1.9-3.7A1.9 1.9 0 0 0 5 2.2z" fill="#fff"/></svg>12 Quay Lane, Porthaven, box 40210</li>
  </ul>

  <div class="color-blocks" aria-hidden="true">
    <span class="color-block color-block--teal"></span>
    <span class="color-block color-block--orchid"></span>
    <span class="color-block color-block--sky"></span>
    <span class="color-block color-block--teal"></span>
    <span class="color-block color-block--blue"></span>
    <span class="color-block color-block--rose"></span>
    <span class="color-block color-block--indigo"></span>
  </div>
</main>
</body>
</html>
```